Gobal construction supply company needs new business card design

I need a business card design for my global supply company using an existing logo. i will be looking to print these on rounded corner cards with the black background version of my logo on the back. on the front white background, my logo again and my simple details.

```html
<!DOCTYPE html>
<html lang="en">
<head>
<meta charset="utf-8">
<title>Harbourline Supply Co — Business Card</title>
<link href="https://fonts.googleapis.com/css2?family=Roboto:wght@400;500;700&display=swap" rel="stylesheet">
<style>
  :root {
    --stage: #3a3a3a;
    --card-light: #f3f3f3;
    --card-dark: #1b1b1b;
    --ink: #111111;
    --text-grey: #444444;
    --brand-red: #e0000f;
    --white: #ffffff;
  }
  * { margin: 0; padding: 0; box-sizing: border-box; }
  html, body { width: 1200px; height: 960px; overflow: hidden; }
  body { background: var(--stage); font-family: "Roboto", sans-serif; position: relative; }

  .card { position: absolute; width: 600px; height: 343px; border-radius: 22px; overflow: hidden; }
  .card-front { left: 186px; top: 113px; background: var(--card-light); }
  .card-back { left: 434px; top: 512px; background: var(--card-dark); }

  .brand-front { position: absolute; left: 36px; top: 80px; display: flex; align-items: center; gap: 10px; }
  .brand-name { font-weight: 700; font-size: 19px; color: var(--ink); letter-spacing: 0.2px; }
  .brand-dot { width: 16px; height: 16px; border-radius: 50%; background: var(--brand-red); }

  .name-band { position: absolute; right: 0; top: 94px; width: 250px; height: 49px; }
  .name-band svg { position: absolute; inset: 0; }
  .person { position: absolute; right: 62px; top: 96px; text-align: right; color: var(--white); }
  .person-name { font-weight: 700; font-size: 21px; line-height: 24px; }
  .person-title { font-weight: 500; font-size: 15px; line-height: 18px; }
  .person-icon { position: absolute; right: 30px; top: 109px; }

  .contacts { position: absolute; right: 62px; top: 176px; list-style: none; text-align: right; }
  .contacts li { font-size: 14px; line-height: 19px; color: var(--text-grey); position: relative; }
  .contacts svg { position: absolute; right: -28px; top: 3px; }

  .address-bar { position: absolute; left: 0; right: 0; top: 290px; height: 28px; background: var(--ink); }
  .address { position: absolute; right: 62px; top: 5px; color: var(--white); font-size: 14px; }
  .address-bar svg { position: absolute; right: 36px; top: 6px; }

  .brand-back { position: absolute; left: 0; right: 0; top: 145px; display: flex; justify-content: center; align-items: center; gap: 14px; }
  .brand-back .brand-name { color: var(--white); font-size: 34px; }
  .brand-back .brand-dot { width: 36px; height: 36px; }
  .back-web { position: absolute; left: 0; right: 0; top: 290px; text-align: center; color: var(--white); font-size: 14px; letter-spacing: 3px; }
</style>
</head>
<body>
  <section class="card card-front">
    <div class="brand-front">
      <span class="brand-name">HARBOURLINE SUPPLY CO</span>
      <span class="brand-dot"></span>
    </div>

    <div class="name-band">
      <svg width="250" height="49" viewBox="0 0 250 49"><polygon points="34,0 250,0 250,49 0,49" fill="#e0000f"/></svg>
    </div>
    <div class="person">
      <div class="person-name">DANA WHITLOW</div>
      <div class="person-title">CEO/Founder</div>
    </div>
    <svg class="person-icon" width="16" height="16" viewBox="0 0 16 16" aria-hidden="true"><circle cx="8" cy="5" r="3.5" fill="#fff"/><path d="M1 15c0-4 3-6 7-6s7 2 7 6z" fill="#fff"/></svg>

    <ul class="contacts">
      <li>512 304 7781<svg width="13" height="13" viewBox="0 0 16 16"><path d="M3 1l3 0 1 4-2 1.5c1 2 2.5 3.5 4.5 4.5L11 9l4 1v3c0 1-1 2-2 2C7 15 1 9 1 3c0-1 1-2 2-2z" fill="#111"/></svg></li>
      <li>512 860 2195<svg width="13" height="13" viewBox="0 0 16 16"><rect x="4" y="0.5" width="8" height="15" rx="1.5" fill="none" stroke="#111" stroke-width="1.6"/><rect x="7" y="12.5" width="2" height="1.2" fill="#111"/></svg></li>
      <li>512 447 6023<svg width="13" height="13" viewBox="0 0 16 16"><rect x="4" y="1" width="8" height="4" fill="#111"/><rect x="1" y="6" width="14" height="6" rx="1" fill="#111"/><rect x="4" y="10" width="8" height="5" fill="#111" stroke="#f3f3f3" stroke-width="1"/></svg></li>
      <li>dana@harbourlinesupply.com<svg width="13" height="13" viewBox="0 0 16 16"><rect x="1" y="3" width="14" height="10" fill="#111"/><path d="M1 3l7 6 7-6" fill="none" stroke="#f3f3f3" stroke-width="1.2"/></svg></li>
      <li>www.harbourlinesupply.com<svg width="13" height="13" viewBox="0 0 16 16"><circle cx="8" cy="8" r="7" fill="#111"/><path d="M4 5c2 0 3 1 2 3s1 3 0 5M10 3c0 2 2 2 3 4" fill="none" stroke="#f3f3f3" stroke-width="1.2"/></svg></li>
    </ul>

    <div class="address-bar">
      <span class="address">2140 Cedar Ridge Road, Portland, Oregon 97205</span>
      <svg width="12" height="17" viewBox="0 0 12 17"><path d="M6 0C2.7 0 0 2.6 0 5.9 0 10 6 17 6 17s6-7 6-11.1C12 2.6 9.3 0 6 0z" fill="#fff"/><circle cx="6" cy="6" r="2.2" fill="#111"/></svg>
    </div>
  </section>

  <section class="card card-back">
    <div class="brand-back">
      <span class="brand-name">HARBOURLINE SUPPLY CO</span>
      <span class="brand-dot"></span>
    </div>
    <div class="back-web">www.harbourlinesupply.com</div>
  </section>
</body>
</html>
```